Business Cards

Need business card design that I can update for new employees and details. Needs to incorporate our logo, be bright and fun (in line with tourism and holidays)
Would like a Map of Western Australia on the front with locations all the caravan parks we own (just purchased Tom Price so please include that as well as others listed on our website).
Target Market(s)
Famillies
Contact Information for Business Card
5 Cards -
Neil Perrow (Director) e: perrow@wattlebay.com.au p: 0491 570 156
Mira Perrow (Director) e: perrow@wattlebay.com.au p: 0491 570 157
Owen Halvey (General Manager) e: halvey@wattlebay.com.au p: 0491 570 158
Helen Halvey (General Manager) e: halvey@wattlebay.com.au p: 0491 570 159
Colin Danby (Training and Operations Manager) - e: danby@wattlebay.com.au p:0491 570 110
Colors
Look and feel

```html
<!DOCTYPE html>
<html lang="en">
<head>
<meta charset="utf-8">
<title>Wattlebay Tourist Parks – Business Card</title>
<link rel="stylesheet" href="https://fonts.googleapis.com/css2?family=Cinzel:wght@400&family=Roboto:wght@400;500&display=swap">
<style>
  :root {
    --bg: #e9e6e1;
    --teal: #45bcc6;
    --teal-light: #62cad1;
    --teal-dark: #2f9ea6;
    --sea-green: #6cc0ad;
    --paper: #f6f6f5;
    --ink-grey: #5a5a5a;
    --card-black: #1d1e20;
    --white: #ffffff;
  }
  * { box-sizing: border-box; margin: 0; padding: 0; }
  html, body { width: 1200px; height: 911px; overflow: hidden; }
  body {
    background: var(--bg);
    display: flex;
    align-items: center;
    justify-content: center;
    gap: 60px;
    font-family: "Roboto", Arial, sans-serif;
  }
  .card {
    position: relative;
    overflow: hidden;
    box-shadow: 0 10px 28px rgba(0,0,0,.22);
  }
  /* Front: portrait */
  .card--front {
    width: 380px;
    height: 640px;
    background: var(--paper);
  }
  .card__wave { position: absolute; inset: 0; width: 100%; height: 100%; }
  .contact {
    position: absolute;
    top: 38px;
    left: 34px;
    right: 24px;
    color: var(--white);
  }
  .contact__name {
    font-size: 22px;
    font-weight: 500;
    letter-spacing: .3px;
    text-transform: uppercase;
    line-height: 1.1;
  }
  .contact__role {
    font-size: 13px;
    text-transform: uppercase;
    letter-spacing: .8px;
    margin-bottom: 22px;
  }
  .contact__list { list-style: none; }
  .contact__item {
    display: flex;
    align-items: center;
    gap: 10px;
    font-size: 13.5px;
    line-height: 1.55;
  }
  .contact__icon { width: 12px; height: 12px; flex: none; fill: var(--white); }

  .brand {
    display: flex;
    align-items: center;
    gap: 14px;
  }
  .brand__mark {
    width: 58px;
    height: 58px;
    background: var(--teal);
    border: 3px solid var(--white);
    outline: 1px solid var(--teal-dark);
  }
  .brand__name {
    font-family: "Cinzel", Georgia, serif;
    font-size: 30px;
    letter-spacing: 3px;
    line-height: 1;
  }
  .brand__tagline {
    font-family: "Cinzel", Georgia, serif;
    font-size: 12px;
    letter-spacing: 4px;
    margin-top: 6px;
  }
  .card--front .brand {
    position: absolute;
    left: 34px;
    bottom: 70px;
    color: var(--ink-grey);
  }

  /* Back: landscape */
  .card--back {
    width: 640px;
    height: 380px;
    background: var(--card-black);
    color: var(--white);
  }
  .card--back .brand {
    position: absolute;
    top: 118px;
    left: 50%;
    transform: translateX(-50%);
  }
  .card--back .brand__mark { width: 74px; height: 74px; }
  .card--back .brand__name { font-size: 38px; }
  .card--back .brand__tagline { font-size: 14px; }
  .website {
    position: absolute;
    bottom: 46px;
    width: 100%;
    text-align: center;
    font-size: 14px;
    letter-spacing: 2.5px;
  }
</style>
</head>
<body>

  <article class="card card--front">
    <svg class="card__wave" viewBox="0 0 380 640" preserveAspectRatio="none" aria-hidden="true">
      <defs>
        <linearGradient id="tealWash" x1="0" y1="0" x2="1" y2="1">
          <stop offset="0" stop-color="#3db6c1"/>
          <stop offset="1" stop-color="#67ccd2"/>
        </linearGradient>
      </defs>
      <path d="M0 0 H380 V352 C312 342 262 290 210 236 C160 184 90 168 0 168 Z" fill="var(--teal-dark)"/>
      <path d="M0 0 H380 V342 C312 332 262 280 210 226 C160 174 90 158 0 158 Z" fill="var(--paper)"/>
      <path d="M0 0 H380 V336 C312 326 262 274 210 220 C160 168 90 152 0 152 Z" fill="url(#tealWash)"/>
    </svg>

    <div class="contact">
      <h1 class="contact__name">Neil Perrow</h1>
      <p class="contact__role">Director</p>
      <ul class="contact__list">
        <li class="contact__item">
          <svg class="contact__icon" viewBox="0 0 24 24"><path d="M6.6 10.8a15 15 0 0 0 6.6 6.6l2.2-2.2a1 1 0 0 1 1-.25 11.4 11.4 0 0 0 3.6.57 1 1 0 0 1 1 1V20a1 1 0 0 1-1 1A17 17 0 0 1 3 4a1 1 0 0 1 1-1h3.5a1 1 0 0 1 1 1c0 1.25.2 2.45.57 3.57a1 1 0 0 1-.25 1z"/></svg>
          0491 570 156
        </li>
        <li class="contact__item">
          <svg class="contact__icon" viewBox="0 0 24 24"><path d="M2 5h20v14H2z M4 7v.5l8 5 8-5V7l-8 5z" fill-rule="evenodd"/></svg>
          perrow@wattlebay.com.au
        </li>
        <li class="contact__item">
          <svg class="contact__icon" viewBox="0 0 24 24"><circle cx="12" cy="12" r="10" fill="none" stroke="#fff" stroke-width="2"/><path d="M2 12h20M12 2c3 3 3 17 0 20M12 2c-3 3-3 17 0 20" fill="none" stroke="#fff" stroke-width="1.6"/></svg>
          www.wattlebay.com.au
        </li>
      </ul>
    </div>

    <div class="brand">
      <div>
        <p class="brand__name">Wattlebay</p>
        <p class="brand__tagline">Tourist Parks</p>
      </div>
      <span class="brand__mark"></span>
    </div>
  </article>

  <article class="card card--back">
    <div class="brand">
      <div>
        <p class="brand__name">Wattlebay</p>
        <p class="brand__tagline">Tourist Parks</p>
      </div>
      <span class="brand__mark"></span>
    </div>
    <p class="website">www.wattlebay.com.au</p>
  </article>

</body>
</html>
```